Create modern and sleek business card for luxury real estate company

We're a "boutique" real estate office looking for a design that gets across a highly modern luxury brand. Blacks and whites are probably the best colors unless we try a silver foil for the logo. I've attached a version of our current logo here. I'd like to swap out the current font on there with Gotham Light Regular.

I'm looking to have one side of the card have the logo with the space for our agents info on the other side.

Target Market(s)

Young professionals in a "luxury" headspace

Industry/Entity Type

Real estate

Contact Information for Business Card

A place for agent name, cell number, website. The slogan "Quietly Redefining Fine Living".

Font styles to use
Other font styles liked:
• Gotham Regular

Colors

Designer to choose only greyscale colors for use in the design.

Requirements
Must have
• Matte black as the background color. Clean lines and use of contrast. A specific design aspect that will use silver foil.
Nice to have
• Up in the air on integrating a QR code
Should not have
• Any houses or other real estate related design (ex: a clip art house)

```html
<!DOCTYPE html>
<html lang="en">
<head>
<meta charset="UTF-8">
<title>Northlane Realty – Business Card</title>
<link rel="stylesheet" href="https://fonts.googleapis.com/css2?family=Montserrat:wght@300;400&family=Oswald:wght@600&family=Roboto:wght@300;400&display=swap">
<style>
  :root {
    --backdrop: #121212;
    --card: #232323;
    --card-edge: #2c2c2c;
    --ink: #ffffff;
    --ink-muted: #bdbdbd;
    --foil: #8f8f8f;
    --rule: #9a9a9a;
  }
  * { margin: 0; padding: 0; box-sizing: border-box; }
  html, body {
    width: 1200px; height: 900px; overflow: hidden;
    background: var(--backdrop);
  }
  .stage {
    width: 1200px; height: 900px;
    display: flex; flex-direction: column;
    align-items: center; justify-content: center; gap: 40px;
  }
  .card {
    width: 700px; height: 400px;
    background: radial-gradient(circle at 50% 40%, #2a2a2a, var(--card) 70%);
    border: 1px solid var(--card-edge);
    box-shadow: 0 12px 30px rgba(0,0,0,.6);
    position: relative;
  }
  /* Front: logo side */
  .card--front {
    display: flex; align-items: center; justify-content: center; gap: 24px;
  }
  .brand-dot {
    width: 84px; height: 84px; border-radius: 50%;
    border: 3px solid var(--foil);
  }
  .brand-name {
    font-family: "Montserrat", sans-serif; font-weight: 400;
    font-size: 46px; line-height: 1.05; letter-spacing: 3px;
    color: var(--foil); text-transform: uppercase;
  }
  /* Back: agent side */
  .card--back { font-family: "Roboto", sans-serif; color: var(--ink); }
  .agent {
    position: absolute; right: 370px; top: 130px; text-align: right;
  }
  .agent-name {
    font-family: "Oswald", sans-serif; font-weight: 600;
    font-size: 34px; letter-spacing: .5px; text-transform: uppercase; line-height: 1.1;
  }
  .agent-title {
    font-family: "Montserrat", sans-serif; font-weight: 300;
    font-size: 15px; color: var(--ink-muted); letter-spacing: .5px;
  }
  .divider {
    position: absolute; left: 348px; top: 130px;
    width: 1px; height: 76px; background: var(--rule);
  }
  .contact {
    position: absolute; left: 370px; top: 136px;
    list-style: none; font-size: 15px; line-height: 22px;
  }
  .contact li { display: flex; align-items: center; gap: 8px; }
  .contact svg { width: 12px; height: 12px; fill: var(--ink); flex: none; }
  .slogan {
    position: absolute; left: 140px; top: 262px;
    font-size: 15px; letter-spacing: .3px;
  }
</style>
</head>
<body>
<main class="stage">
  <section class="card card--front" aria-label="Card front">
    <span class="brand-dot"></span>
    <span class="brand-name">Northlane<br>Realty</span>
  </section>

  <section class="card card--back" aria-label="Card back">
    <div class="agent">
      <p class="agent-name">Adrian Vale</p>
      <p class="agent-title">Founder &amp; CEO</p>
    </div>
    <span class="divider"></span>
    <ul class="contact">
      <li>
        <svg viewBox="0 0 24 24"><path d="M6.6 10.8a15 15 0 0 0 6.6 6.6l2.2-2.2a1 1 0 0 1 1-.25 11.4 11.4 0 0 0 3.6.57 1 1 0 0 1 1 1V20a1 1 0 0 1-1 1A17 17 0 0 1 3 4a1 1 0 0 1 1-1h3.5a1 1 0 0 1 1 1c0 1.25.2 2.45.57 3.6a1 1 0 0 1-.25 1z"/></svg>
        (555) 014-2290
      </li>
      <li>
        <svg viewBox="0 0 24 24"><path d="M2 5h20v14H2z M2 5l10 8 10-8" fill="none" stroke="#fff" stroke-width="2"/></svg>
        hello@northlanehomes.com
      </li>
      <li>
        <svg viewBox="0 0 24 24"><g fill="none" stroke="#fff" stroke-width="2"><circle cx="12" cy="12" r="10"/><ellipse cx="12" cy="12" rx="4" ry="10"/><path d="M2 12h20"/></g></svg>
        www.northlanehomes.com
      </li>
    </ul>
    <p class="slogan">Quietly Redefining Fine Living</p>
  </section>
</main>
</body>
</html>
```